Wine Label Design-Hollow Creek Vineyard

Hollow Creek Vineyard is in the Barossa Valley in South Australia. The Barossa is recognized as Australia's premier wine region, producing Australia's icon wines and some " new takes on traditional".
This family owned and operated vineyard grows some exceptionally high quality fruit. Most of the fruit is sold and used for some of Australia's most iconic wines. Small quantities are retained by the owners for some wines with very limited availability. (Wines were previously sold as Brackwell Vineyards Hollow Creek ( Shiraz, Cabernet etc).

The wines will in the future be labeled simply ‘Hollow Creek Vineyard’. The label will launch this new identity for the single family single vineyard and its high quality wines which are a true expression of the vineyard and derive from the Hollow Creek common to this ancient area (800-2000 million years old).
The label should reflect
• Single vineyard, family owned
• vines in very old rock & soils
• High quality & reliability
• Edgy but true, design based thinking (Please note:blue is generally seen as an unacceptable colour for a wine label?? Don’t ask me why)

The wines will be sold mostly direct in Australia ( ie not through retail stores), with limited export to Asia, Scandinavia and Canada.
There are three quality levels and price points in the portfolio
1. Entry level premium for everyday drinking for discriminating drinkers-approx AUD20
2. Super Premium-approx AUD30
3. Limited Release ultlra premium-AUD75-90?
We envisage three variations on the label but with an obvious & common design element. This design element should be able to be used for corporate identification and promotion
The paper stock will be waterproof and self adhesive. Our preference is for designs that engage the user by appealing to both sight and touch. It is preferred that textures be added eg embossing, high build varnish etc-rather than be a facet of the stock itself.
For information on statutory label requirements refer to www.vintnerregistry-example.com . In brief
o Front label need not show any mandatory information. However we would prefer Variety, Barossa Valley, Year and alcohol to be shown on the front label
o Back label should show all mandatories and allow for a bar code
Updates

Project Deadline Extended
Reason: I've had a problem with my wireless broadband account and reception has been intermittent to say the least to the extent that I switched off at the weekend. Just going downtown now for a 'polite discussion' with my service provider.

Project Deadline Extended
Reason: I have receiver insufficient designs of quality which we would consider. Too many designs have a "cut and paste" appearance - too few exhibit an original art/design element which truly identifies the product.

Gals & Guys

most of the designs submitted lack punch and originality and are totally unmemorable.
Please-get on Searcho or whatever enter "Wine Label Designs" and do some research b4 u waste your time and mine. Formulaic cut and paste will not win the day. That's not to say that cut and paste can't work-but it must have some originality, impact and command attention. Please surprise me.

Following on from a question from a designer about who is our competition and what we are looking for I sent the following 
"I don't think I can add anything new. Read the brief and comments again and research wine labels on the web. In 30 minutes you'll get a good idea of the creative edgy designs in the industry. There are a plethora of collections. Our competition-anyone with a label. In 2010 there were over 2400 "producers" in other words 2400 producers with at least one label. In fact there are over 25000 Australian wines and then the numerous imported wines.

Target Market(s)

$20 people who budget everyday but have graduated from drinking 'entry level' wines. These people will likely fit into Cat. (b) in the $30 wine

$30 (a) will not over-compromise on some everyday discretionary expenditure.(b) might buy for special occasions

$70-$90 Professional/successful people with high disposable/discretionary income not particularly worried about recession. wine geeks.

Industry/Entity Type

Retail

Requirements
Must have
• identifiable element across range of wines

```html
<!DOCTYPE html>
<html lang="en">
<head>
<meta charset="utf-8">
<title>Hollow Creek Vineyard – Label Range</title>
<link href="https://fonts.googleapis.com/css2?family=Pinyon+Script&family=Tinos:wght@400;700&display=swap" rel="stylesheet">
<style>
  :root{
    --paper:#ffffff;
    --navy-deep:#050830;
    --navy:#0c1356;
    --navy-glow:#1c2d92;
    --stripe:#8fb8ff;
    --stripe-soft:rgba(70,130,255,.55);
    --gold:#e6c77a;
    --gold-dark:#b08a3a;
    --ink-light:#f4f1e8;
    --tier-premium:#0d2a8a;
    --tier-premium-hi:#2650c8;
    --tier-super:#0f6a1c;
    --tier-super-hi:#2a9a32;
    --tier-ultra:#8e0c0c;
    --tier-ultra-hi:#d42020;
    --bottle:#1a1414;
  }
  *{box-sizing:border-box;margin:0;padding:0}
  html,body{width:1200px;height:900px;overflow:hidden;background:var(--paper)}
  body{position:relative;font-family:"Tinos","Times New Roman",serif}

  .label{
    position:absolute;width:391px;height:346px;border-radius:26px;overflow:hidden;
    background:
      linear-gradient(90deg,transparent 16%,var(--stripe-soft) 19.5%,var(--stripe) 21%,var(--stripe-soft) 22.5%,transparent 26%),
      radial-gradient(ellipse at 50% 40%,var(--navy-glow),var(--navy) 60%,var(--navy-deep));
  }
  .label--premium{left:187px;top:84px;--tier:var(--tier-premium);--tier-hi:var(--tier-premium-hi)}
  .label--super{left:622px;top:84px;--tier:var(--tier-super);--tier-hi:var(--tier-super-hi)}
  .label--ultra{left:405px;top:468px;--tier:var(--tier-ultra);--tier-hi:var(--tier-ultra-hi)}

  .label__frame{position:absolute;inset:12px;border:2px solid var(--gold);border-radius:16px}

  .label__mark{position:absolute;top:34px;left:0;right:0;display:flex;flex-direction:column;align-items:center;gap:6px}
  .label__mark-square{width:34px;height:34px;background:var(--tier)}
  .label__mark-name{font-size:11px;font-weight:700;letter-spacing:3px;color:var(--gold);text-transform:uppercase}

  .label__rule{position:absolute;left:60px;right:60px;height:1px;
    background:linear-gradient(90deg,transparent,var(--gold) 20%,var(--gold) 80%,transparent)}
  .label__rule--top{top:106px}
  .label__rule--bottom{top:162px}

  .label__title{position:absolute;top:112px;left:0;right:0;text-align:center;
    font-family:"Pinyon Script",cursive;font-size:31px;color:var(--gold);white-space:nowrap}
  .label__year{position:absolute;top:170px;left:0;right:0;text-align:center;font-size:16px;font-weight:700;color:var(--gold)}
  .label__region{position:absolute;top:190px;left:0;right:0;text-align:center;font-size:12px;font-weight:700;color:var(--ink-light)}

  .label__band{position:absolute;top:216px;left:14px;right:14px;height:56px;
    border-top:1px solid var(--gold);border-bottom:1px solid var(--gold);
    background:
      linear-gradient(90deg,transparent 16%,rgba(255,255,255,.35) 21%,transparent 26%),
      linear-gradient(90deg,var(--tier),var(--tier-hi) 30%,var(--tier) 70%,var(--navy-deep));
    text-align:center;padding-top:9px}
  .label__tier{font-size:19px;font-weight:700;letter-spacing:3px;color:var(--gold);line-height:1}
  .label__variety{font-size:12px;color:var(--ink-light);margin-top:3px}

  .label__facts{position:absolute;top:290px;left:36px;right:36px;display:flex;justify-content:space-between;
    font-size:12px;color:var(--ink-light)}
  .label__facts-rule{position:absolute;top:308px;left:36px;right:36px;height:1px;background:var(--gold)}
  .label__address{position:absolute;top:313px;left:0;right:0;text-align:center;font-size:8.5px;color:var(--ink-light)}

  .bottle{position:absolute;left:888px;top:465px;width:96px;height:355px}
</style>
</head>
<body>

  <section class="label label--premium">
    <div class="label__frame"></div>
    <div class="label__mark"><span class="label__mark-square"></span><span class="label__mark-name">Hollow Creek</span></div>
    <div class="label__rule label__rule--top"></div>
    <h2 class="label__title">Hollow Creek Vineyard</h2>
    <div class="label__rule label__rule--bottom"></div>
    <p class="label__year">2006</p>
    <p class="label__region">Barossa Valley - South Australia</p>
    <div class="label__band"><p class="label__tier">PREMIUM</p><p class="label__variety">Cabernet Sauvignon</p></div>
    <div class="label__facts"><span>750 mL</span><span>Standard drinks - 8,3</span><span>13,5% ALC/VOL.</span></div>
    <div class="label__facts-rule"></div>
    <p class="label__address">Hollow Creek Vineyard , Barossa Valley , Ridge Lane 14/20, South Australia</p>
  </section>

  <section class="label label--super">
    <div class="label__frame"></div>
    <div class="label__mark"><span class="label__mark-square"></span><span class="label__mark-name">Hollow Creek</span></div>
    <div class="label__rule label__rule--top"></div>
    <h2 class="label__title">Hollow Creek Vineyard</h2>
    <div class="label__rule label__rule--bottom"></div>
    <p class="label__year">2006</p>
    <p class="label__region">Barossa Valley - South Australia</p>
    <div class="label__band"><p class="label__tier">SUPER PREMIUM</p><p class="label__variety">Cabernet Sauvignon</p></div>
    <div class="label__facts"><span>750 mL</span><span>Standard drinks - 8,3</span><span>13,5% ALC/VOL.</span></div>
    <div class="label__facts-rule"></div>
    <p class="label__address">Hollow Creek Vineyard , Barossa Valley , Ridge Lane 14/20, South Australia</p>
  </section>

  <section class="label label--ultra">
    <div class="label__frame"></div>
    <div class="label__mark"><span class="label__mark-square"></span><span class="label__mark-name">Hollow Creek</span></div>
    <div class="label__rule label__rule--top"></div>
    <h2 class="label__title">Hollow Creek Vineyard</h2>
    <div class="label__rule label__rule--bottom"></div>
    <p class="label__year">2006</p>
    <p class="label__region">Barossa Valley - South Australia</p>
    <div class="label__band"><p class="label__tier">ULTRA PREMIUM</p><p class="label__variety">Cabernet Sauvignon</p></div>
    <div class="label__facts"><span>750 mL</span><span>Standard drinks - 8,3</span><span>13,5% ALC/VOL.</span></div>
    <div class="label__facts-rule"></div>
    <p class="label__address">Hollow Creek Vineyard , Barossa Valley , Ridge Lane 14/20, South Australia</p>
  </section>

  <svg class="bottle" viewBox="0 0 96 355" aria-label="Bottle with Ultra Premium label">
    <defs>
      <linearGradient id="capsuleShade" x1="0" x2="1">
        <stop offset="0" stop-color="#7a0a0a"/><stop offset=".5" stop-color="#d42020"/><stop offset="1" stop-color="#6a0808"/>
      </linearGradient>
      <linearGradient id="miniLabel" x1="0" x2="1">
        <stop offset="0" stop-color="#0c1356"/><stop offset=".2" stop-color="#3a68d8"/><stop offset=".28" stop-color="#0c1356"/><stop offset="1" stop-color="#050830"/>
      </linearGradient>
    </defs>
    <path d="M35 30 H61 V110 C61 140 96 140 96 175 V355 H0 V175 C0 140 35 140 35 110 Z" fill="var(--bottle)"/>
    <rect x="34" y="0" width="28" height="48" rx="2" fill="url(#capsuleShade)"/>
    <rect x="34" y="44" width="28" height="4" fill="#5a0606"/>
    <rect x="16" y="120" width="4" height="220" rx="2" fill="#ffffff" opacity=".9"/>
    <rect x="0" y="182" width="96" height="84" fill="url(#miniLabel)"/>
    <rect x="3" y="185" width="90" height="78" fill="none" stroke="#e6c77a" stroke-width=".8"/>
    <rect x="44" y="190" width="8" height="8" fill="#8e0c0c"/>
    <text x="48" y="214" text-anchor="middle" font-family="Pinyon Script, cursive" font-size="9" fill="#e6c77a">Hollow Creek Vineyard</text>
    <text x="48" y="224" text-anchor="middle" font-family="Tinos, serif" font-size="4" font-weight="700" fill="#e6c77a">2006</text>
    <text x="48" y="230" text-anchor="middle" font-family="Tinos, serif" font-size="3.2" fill="#f4f1e8">Barossa Valley - South Australia</text>
    <rect x="3" y="234" width="90" height="13" fill="#8e0c0c"/>
    <text x="48" y="242" text-anchor="middle" font-family="Tinos, serif" font-size="5" font-weight="700" fill="#e6c77a">ULTRA PREMIUM</text>
    <text x="48" y="246" text-anchor="middle" font-family="Tinos, serif" font-size="2.6" fill="#f4f1e8">Cabernet Sauvignon</text>
    <line x1="10" y1="254" x2="86" y2="254" stroke="#e6c77a" stroke-width=".4"/>
  </svg>

</body>
</html>
```